Brightline Energy Product Distribution Brochure

We are looking to have our current brochure for our customers completely redesigned...the idea is to present the relevant information in an attractive way . Our website is brightlineenergyco.example where you can find more information about us. We have included a file with a rough idea of the page order and what each should include but feel free to adapt based on design. The example provided is only for context and doesnt have to be maintained. We will be using the brochure both digitally and in print form. As long as it reads easily and is eye catching, the design can be horizontal or vertical.Final deliverable should be indesign file.

"Our Brands" page: should be limited to one page (space being enough) where it has the header for each one (for example diesel generators) space for one or two lines of text and then the corresponding logos for each of the five categories
Updates

For those asking: the "our brands" page should be a single page layout where there is a header with the corresponding section and space for maybe one line of text followed by the two logos for that category. Each of the product pages should be similar in fashion to the one in the document attached: a photo of the product with some white space and space for the text to be included. We will be posting additional examples today

Target Market(s)

We want to present it to customers both digitally and in print so they can see our products

Industry/Entity Type

Power Generation

Font styles to use
Serif

Requirements
Must have
• Eye catching and able to present the information in a presentable fashion. Rest is up to you.
Nice to have
• Should incorporate the colors of our logo but can also add other depending on design

```html
<!DOCTYPE html>
<html lang="en">
<head>
<meta charset="utf-8">
<title>Brightline Energy – Distributor Program Guide</title>
<link href="https://fonts.googleapis.com/css2?family=Raleway:wght@300;400;600;700&family=Montserrat:wght@400;600;700&display=swap" rel="stylesheet">
<style>
  :root{
    --bg:#b3b3b3;
    --paper:#ffffff;
    --blue:#0b5cb8;
    --blue-deep:#0849a0;
    --sky:#3fa9f5;
    --ink:#333333;
    --muted:#8a8a8a;
    --charcoal:#3a3a3a;
    --charcoal-dark:#2c2c2c;
    --gold:#f2b51c;
    --steel-light:#e4e6ea;
    --steel-dark:#5b6068;
  }
  *{box-sizing:border-box;margin:0;padding:0}
  html,body{width:1200px;height:640px;overflow:hidden;background:var(--bg)}
  body{position:relative;font-family:"Montserrat",sans-serif;color:var(--ink)}

  .page{position:absolute;width:157px;height:222px;background:var(--paper);overflow:hidden;box-shadow:0 1px 3px rgba(0,0,0,.18)}
  .row-1{top:78px}.row-2{top:346px}
  .col-1{left:29px}.col-2{left:193px}.col-3{left:357px}.col-4{left:521px}
  .col-5{left:685px}.col-6{left:849px}.col-7{left:1014px}

  /* geometric system */
  .outline{position:absolute;width:110px;height:110px;border:.6px solid var(--sky);transform:rotate(45deg);left:100px;top:-30px}
  .outline.low{left:-70px;top:130px;width:90px;height:90px}
  .blue-right{position:absolute;inset:0;background:linear-gradient(160deg,var(--blue),var(--blue-deep));clip-path:polygon(100% 36%,100% 100%,42% 100%)}
  .blue-left{position:absolute;inset:0;background:var(--blue);clip-path:polygon(0 60%,30% 92%,0 92%)}
  .blue-strip{position:absolute;left:0;right:0;bottom:0;height:11%;background:var(--blue-deep)}
  .diamond{position:absolute;left:36px;top:104px;width:88px;height:88px;background:var(--paper);transform:rotate(45deg);box-shadow:2px 3px 8px rgba(0,0,0,.35)}
  .diamond.small{left:86px;top:134px;width:58px;height:58px}
  .product{position:absolute;left:48px;top:126px;width:64px;height:46px;border-radius:2px;background:linear-gradient(135deg,var(--steel-light),var(--steel-dark))}
  .product.tall{left:60px;top:118px;width:40px;height:58px}
  .product.small{left:95px;top:150px;width:40px;height:26px}

  /* text */
  .page-label{position:absolute;top:8px;left:14px;font-size:3.4px;letter-spacing:.2px;color:var(--muted);text-transform:uppercase}
  .page-label::before{content:"";display:inline-block;width:6px;height:.5px;background:var(--sky);vertical-align:middle;margin-right:3px}
  .brand-mark{position:absolute;top:7px;right:10px;display:flex;align-items:center;gap:2px;font-family:"Raleway",sans-serif;font-weight:600;font-size:3.6px;color:var(--ink);text-transform:uppercase}
  .brand-mark .dot{width:5px;height:5px;background:var(--gold)}
  .page-title{position:absolute;top:36px;left:14px;font-family:"Raleway",sans-serif;font-weight:300;font-size:10px;line-height:1.1;color:var(--ink);text-transform:uppercase}
  .subhead{position:absolute;top:58px;left:14px;font-size:4px;font-weight:700;color:var(--blue);text-transform:uppercase}
  .body-copy{position:absolute;top:64px;left:14px;width:86px;font-size:2.6px;line-height:1.45;color:var(--muted)}
  .footer{position:absolute;bottom:5px;left:14px;display:flex;gap:14px;font-size:2.6px;color:#fff;text-transform:uppercase}

  /* cover */
  .cover-top{position:absolute;left:0;right:0;top:0;height:48%;background:radial-gradient(circle at 70% 30%,#4a4a4a,var(--charcoal-dark))}
  .cover-title{position:absolute;top:34px;left:18px;font-family:"Raleway",sans-serif;font-weight:700;font-size:10px;line-height:1.15;color:#fff;text-transform:uppercase}
  .cover-title span{color:var(--sky)}
  .cover-rule{position:absolute;top:60px;left:18px;width:68px;height:.6px;background:#fff}
  .cover-sub{position:absolute;top:63px;left:18px;font-family:"Raleway",sans-serif;font-size:4.2px;line-height:1.35;color:var(--sky);text-transform:uppercase}
  .cover-brand{position:absolute;top:110px;left:14px;display:flex;align-items:center;gap:3px;font-family:"Raleway",sans-serif;font-weight:600;font-size:5px;color:var(--ink);text-transform:uppercase}
  .cover-brand .dot{width:8px;height:8px;background:var(--gold)}
  .back-brand{position:absolute;top:48px;left:16px;display:flex;align-items:center;gap:3px;font-family:"Raleway",sans-serif;font-weight:600;font-size:7px;color:#fff;text-transform:uppercase}
  .back-brand .dot{width:10px;height:10px;background:var(--gold)}
  .contact{position:absolute;left:14px;top:170px;font-size:2.6px;line-height:1.6;color:#fff}
  .contact h4{font-size:3.6px;font-weight:700;margin-bottom:2px}
  .contact li{list-style:none;display:flex;align-items:center;gap:3px}
  .contact svg{width:4px;height:4px;fill:var(--sky)}
  .contact .web{margin-top:3px;font-weight:600}

  /* index */
  .toc{position:absolute;top:52px;left:14px;width:118px;list-style:none}
  .toc li{display:flex;align-items:center;gap:3px;font-size:3px;font-weight:700;color:var(--ink);margin-bottom:4.2px}
  .toc li::before{content:"";width:2px;height:2px;background:var(--blue);flex:none}
  .toc .lead{flex:1;border-bottom:.4px dotted var(--muted)}

  /* brands */
  .badge{position:absolute;width:11px;height:11px;border:.4px solid #d5d5d5;background:#fff;transform:rotate(45deg)}
  .badge.dark{background:#111;border-color:#111}
  .badge-inner{position:absolute;inset:3px;background:#c9ccd2}
  .badge.dark .badge-inner{background:#555}
  .brand-group{position:absolute;font-size:2.8px;line-height:1.45;color:var(--ink);text-transform:uppercase}
  .brand-group b{display:block;font-size:3px;color:var(--ink)}
  .brand-group b::before{content:"› ";color:var(--blue)}
</style>
</head>
<body>

<!-- Cover -->
<section class="page row-1 col-1">
  <div class="cover-top"></div>
  <h1 class="cover-title">Distributor<br><span>Program Guide</span></h1>
  <div class="cover-rule"></div>
  <p class="cover-sub">Diesel generators,<br>alternators &amp; parts</p>
  <div class="blue-right"></div><div class="blue-left"></div><div class="blue-strip"></div>
  <div class="diamond"></div>
  <div class="product" role="img" aria-label="Diesel generator sets product photo"></div>
  <div class="cover-brand"><span class="dot"></span>Brightline Energy</div>
</section>

<!-- Index -->
<section class="page row-1 col-2">
  <span class="page-label">Index</span>
  <div class="brand-mark"><span class="dot"></span>Brightline Energy</div>
  <h2 class="page-title">Table of content</h2>
  <ul class="toc">
    <li>About our company story<span class="lead"></span>03</li>
    <li>Our brands and partners<span class="lead"></span>04</li>
    <li>Our products at glance<span class="lead"></span>05</li>
    <li>Standby and prime generators<span class="lead"></span>06</li>
    <li>Rental generators and alternators<span class="lead"></span>08</li>
    <li>Alternator parts and controllers<span class="lead"></span>10</li>
    <li>Transfer switches for sites<span class="lead"></span>12</li>
    <li>Our distributors and contacts<span class="lead"></span>13</li>
  </ul>
  <div class="outline low"></div>
  <div class="blue-right"></div><div class="blue-strip"></div>
  <div class="diamond small"></div>
  <div class="product small" role="img" aria-label="Diesel generator sets product photo"></div>
  <div class="footer"><span>2</span><span>brightlineenergyco.example</span></div>
</section>

<!-- About -->
<section class="page row-1 col-3">
  <span class="page-label">About us</span>
  <div class="brand-mark"><span class="dot"></span>Brightline Energy</div>
  <h2 class="page-title">About our<br>company</h2>
  <p class="body-copy" style="top:60px"><b>BRIGHTLINE ENERGY LIMITED INC.</b> is a supplier of diesel generators, transfer switches, controllers, voltage regulators, engine and alternator parts, with a full range of products for power generation.</p>
  <div class="outline"></div>
  <div class="blue-right"></div><div class="blue-left"></div><div class="blue-strip"></div>
  <div class="diamond"></div>
  <div class="product" role="img" aria-label="Diesel generator sets product photo"></div>
  <div class="footer"><span>3</span><span>brightlineenergyco.example</span></div>
</section>

<!-- Brands -->
<section class="page row-1 col-4">
  <span class="page-label">Our brands</span>
  <div class="brand-mark"><span class="dot"></span>Brightline Energy</div>
  <h2 class="page-title">Our brands</h2>
  <div class="badge" style="left:18px;top:56px"><span class="badge-inner"></span></div>
  <div class="badge" style="left:36px;top:56px"><span class="badge-inner"></span></div>
  <div class="badge" style="left:82px;top:56px"><span class="badge-inner"></span></div>
  <div class="badge" style="left:100px;top:56px"><span class="badge-inner"></span></div>
  <div class="brand-group" style="left:14px;top:74px"><b>Diesel generators</b>Voltaris<br>Northfield-Marr</div>
  <div class="brand-group" style="left:78px;top:74px"><b>Controls</b>Coastline Controls<br>Marr</div>
  <div class="badge" style="left:18px;top:102px"><span class="badge-inner"></span></div>
  <div class="badge" style="left:36px;top:102px"><span class="badge-inner"></span></div>
  <div class="badge dark" style="left:82px;top:102px"><span class="badge-inner"></span></div>
  <div class="badge" style="left:100px;top:102px"><span class="badge-inner"></span></div>
  <div class="brand-group" style="left:14px;top:120px"><b>Alternator parts</b>Ashford-Kelt<br>Rowan Pell</div>
  <div class="brand-group" style="left:78px;top:120px"><b>AC alternators</b>Ashford-Kelt<br>Rowan Pell</div>
  <div class="badge" style="left:18px;top:146px"><span class="badge-inner"></span></div>
  <div class="badge" style="left:36px;top:146px"><span class="badge-inner"></span></div>
  <div class="brand-group" style="left:14px;top:164px"><b>Transfer switches</b>Aston Relay<br>Tamworth</div>
  <div class="outline"></div>
  <div class="blue-right"></div><div class="blue-strip"></div>
  <div class="diamond small"></div>
  <div class="product small" role="img" aria-label="Diesel generator sets product photo"></div>
  <div class="footer"><span>4</span><span>brightlineenergyco.example</span></div>
</section>

<!-- Product pages -->
<section class="page row-1 col-5">
  <span class="page-label">Our stock</span>
  <div class="brand-mark"><span class="dot"></span>Brightline Energy</div>
  <h2 class="page-title">Our products</h2>
  <h3 class="subhead">Controllers</h3>
  <p class="body-copy">Reliable diesel power systems built for demanding sites, backed by expert support, fast shipping and a dealer network ready to serve every customer across the region.</p>
  <div class="outline"></div>
  <div class="blue-right"></div><div class="blue-left"></div><div class="blue-strip"></div>
  <div class="diamond"></div>
  <div class="product" role="img" aria-label="Diesel generator sets product photo"></div>
  <div class="footer"><span>5</span><span>brightlineenergyco.example</span></div>
</section>

<section class="page row-1 col-6">
  <span class="page-label">Our stock</span>
  <div class="brand-mark"><span class="dot"></span>Brightline Energy</div>
  <h2 class="page-title">Standby generators</h2>
  <h3 class="subhead">Controllers</h3>
  <p class="body-copy">Reliable diesel power systems built for demanding sites, backed by expert support, fast shipping and a dealer network ready to serve every customer across the region.</p>
  <div class="outline"></div>
  <div class="blue-right"></div><div class="blue-left"></div><div class="blue-strip"></div>
  <div class="diamond"></div>
  <div class="product tall" role="img" aria-label="Voltage regulator board product photo"></div>
  <div class="footer"><span>6</span><span>brightlineenergyco.example</span></div>
</section>

<section class="page row-1 col-7">
  <span class="page-label">Our stock</span>
  <div class="brand-mark"><span class="dot"></span>Brightline Energy</div>
  <h2 class="page-title">Prime generators</h2>
  <h3 class="subhead">Controllers</h3>
  <p class="body-copy">Reliable diesel power systems built for demanding sites, backed by expert support, fast shipping and a dealer network ready to serve every customer across the region.</p>
  <div class="outline"></div>
  <div class="blue-right"></div><div class="blue-left"></div><div class="blue-strip"></div>
  <div class="diamond"></div>
  <div class="product" role="img" aria-label="Trailer mounted generator product photo"></div>
  <div class="footer"><span>7</span><span>brightlineenergyco.example</span></div>
</section>

<section class="page row-2 col-1">
  <span class="page-label">Our stock</span>
  <div class="brand-mark"><span class="dot"></span>Brightline Energy</div>
  <h2 class="page-title">Rental generators</h2>
  <h3 class="subhead">Controllers</h3>
  <p class="body-copy">Reliable diesel power systems built for demanding sites, backed by expert support, fast shipping and a dealer network ready to serve every customer across the region.</p>
  <div class="outline"></div>
  <div class="blue-right"></div><div class="blue-left"></div><div class="blue-strip"></div>
  <div class="diamond"></div>
  <div class="product" role="img" aria-label="Alternator unit product photo"></div>
  <div class="footer"><span>8</span><span>brightlineenergyco.example</span></div>
</section>

<section class="page row-2 col-2">
  <span class="page-label">Our stock</span>
  <div class="brand-mark"><span class="dot"></span>Brightline Energy</div>
  <h2 class="page-title">AC alternators</h2>
  <h3 class="subhead">Controllers</h3>
  <p class="body-copy">Reliable diesel power systems built for demanding sites, backed by expert support, fast shipping and a dealer network ready to serve every customer across the region.</p>
  <div class="outline"></div>
  <div class="blue-right"></div><div class="blue-left"></div><div class="blue-strip"></div>
  <div class="diamond"></div>
  <div class="product" role="img" aria-label="AC alternator product photo"></div>
  <div class="footer"><span>9</span><span>brightlineenergyco.example</span></div>
</section>

<section class="page row-2 col-3">
  <span class="page-label">Our stock</span>
  <div class="brand-mark"><span class="dot"></span>Brightline Energy</div>
  <h2 class="page-title">Alternator parts</h2>
  <h3 class="subhead">Controllers</h3>
  <p class="body-copy">Reliable diesel power systems built for demanding sites, backed by expert support, fast shipping and a dealer network ready to serve every customer across the region.</p>
  <div class="outline"></div>
  <div class="blue-right"></div><div class="blue-left"></div><div class="blue-strip"></div>
  <div class="diamond"></div>
  <div class="product tall" role="img" aria-label="Voltage regulator board product photo"></div>
  <div class="footer"><span>10</span><span>brightlineenergyco.example</span></div>
</section>

<section class="page row-2 col-4">
  <span class="page-label">Our stock</span>
  <div class="brand-mark"><span class="dot"></span>Brightline Energy</div>
  <h2 class="page-title">Controllers</h2>
  <h3 class="subhead">Controllers</h3>
  <p class="body-copy">Reliable diesel power systems built for demanding sites, backed by expert support, fast shipping and a dealer network ready to serve every customer across the region.</p>
  <div class="outline"></div>
  <div class="blue-right"></div><div class="blue-left"></div><div class="blue-strip"></div>
  <div class="diamond"></div>
  <div class="product" role="img" aria-label="Generator control module product photo" style="background:linear-gradient(135deg,#3a3d42,#111)"></div>
  <div class="footer"><span>11</span><span>brightlineenergyco.example</span></div>
</section>

<section class="page row-2 col-5">
  <span class="page-label">Our stock</span>
  <div class="brand-mark"><span class="dot"></span>Brightline Energy</div>
  <h2 class="page-title">Transfer switches</h2>
  <h3 class="subhead">Controllers</h3>
  <p class="body-copy">Reliable diesel power systems built for demanding sites, backed by expert support, fast shipping and a dealer network ready to serve every customer across the region.</p>
  <div class="outline"></div>
  <div class="blue-right"></div><div class="blue-left"></div><div class="blue-strip"></div>
  <div class="diamond"></div>
  <div class="product tall" role="img" aria-label="Automatic transfer switch cabinet product photo"></div>
  <div class="footer"><span>12</span><span>brightlineenergyco.example</span></div>
</section>

<section class="page row-2 col-6">
  <span class="page-label">Our stock</span>
  <div class="brand-mark"><span class="dot"></span>Brightline Energy</div>
  <h2 class="page-title">Our distributors</h2>
  <h3 class="subhead">Controllers</h3>
  <p class="body-copy">Reliable diesel power systems built for demanding sites, backed by expert support, fast shipping and a dealer network ready to serve every customer across the region.</p>
  <div class="outline"></div>
  <div class="blue-right"></div><div class="blue-left"></div><div class="blue-strip"></div>
  <div class="diamond"></div>
  <div class="product" role="img" aria-label="Diesel generator sets product photo"></div>
  <div class="footer"><span>13</span><span>brightlineenergyco.example</span></div>
</section>

<!-- Back cover -->
<section class="page row-2 col-7">
  <div class="cover-top"></div>
  <div class="back-brand"><span class="dot"></span>Brightline Energy</div>
  <div class="blue-right" style="clip-path:polygon(100% 30%,100% 100%,0 100%,0 72%)"></div>
  <div class="diamond small" style="left:84px;top:116px"></div>
  <div class="product small" role="img" aria-label="Diesel generator sets product photo" style="top:132px"></div>
  <div class="contact">
    <h4>Contact Us</h4>
    <ul>
      <li><svg viewBox="0 0 10 10"><path d="M5 0a3.5 3.5 0 0 0-3.5 3.5C1.5 6 5 10 5 10s3.5-4 3.5-6.5A3.5 3.5 0 0 0 5 0zm0 5a1.4 1.4 0 1 1 0-2.8A1.4 1.4 0 0 1 5 5z"/></svg>1200 Harbor Way, Suite 4, Austin, TX 78701, USA</li>
      <li><svg viewBox="0 0 10 10"><path d="M2 0l2 2.5-1 1.5a6 6 0 0 0 3 3l1.5-1L10 8l-1.5 2C4 10 0 6 0 1.5z"/></svg>1-800-555-0142</li>
      <li><svg viewBox="0 0 10 10"><path d="M0 2h10v6H0zm0 0l5 3.5L10 2"/></svg>info@brightlineenergyco.example</li>
    </ul>
    <p class="web">www.brightlineenergyco.example</p>
  </div>
</section>

</body>
</html>
```